Maple n Brook - Contact/Landing Page

I need a landing page which will essentially be the page that customers will go to from the 'website' link on QTV listing. It will provide a short overview of services which need to be selectable. a little further down can capture some contact details followed by a large Submit Now button etc...

I have some icon/logo's that can be utilised at the bottom of the page as industry type references.

Target Market(s)

End of Lease Cleaning Services

Industry/Entity Type

Cleaning Service

Colors

Designer to choose colors to be used in the design.

Requirements
Must have
• As per description
Should not have
• Colours to match my website maplenbrook.com.au

```html
<!DOCTYPE html>
<html lang="en">
<head>
<meta charset="utf-8">
<title>Maple n Brook</title>
<link href="https://fonts.googleapis.com/css2?family=Oswald:wght@500;700&family=Roboto:wght@300;400;500&family=Roboto+Slab:wght@500&display=swap" rel="stylesheet">
<style>
:root{
  --blue:#1778c0;
  --blue-dark:#136bae;
  --blue-light:#4aa3e3;
  --grey-head:#b4b6ba;
  --text:#555a60;
  --ink:#1d1f24;
  --panel:#f4f4f4;
  --footer:#23252f;
  --white:#fff;
}
*{box-sizing:border-box;margin:0;padding:0}
html,body{width:1200px;height:2582px;overflow:hidden;background:var(--white);font-family:'Roboto',sans-serif;color:var(--text)}
.page{position:relative;width:1200px;height:2582px}
.hero{position:absolute;left:0;top:0;width:1200px;height:648px;background:var(--blue);border-bottom-right-radius:260px 168px}
.menu-toggle{position:absolute;left:1070px;top:43px}
.brand{position:absolute;left:0;top:230px;width:1200px;text-align:center;display:flex;align-items:center;justify-content:center;gap:22px}
.brand-dot{width:64px;height:64px;border-radius:50%;background:var(--blue-light)}
.brand-name{font-family:'Oswald',sans-serif;font-weight:700;font-size:72px;color:var(--white);letter-spacing:1px}
.tagline{position:absolute;top:500px;width:1200px;text-align:center;font-family:'Roboto Slab',serif;font-weight:500;font-size:27px;color:var(--white);word-spacing:1px}
.tagline span{margin:0 18px}
.section-title{position:absolute;width:1200px;text-align:center;font-family:'Oswald',sans-serif;font-weight:700;font-size:50px;letter-spacing:1px}
.section-title .a{color:var(--blue)} .section-title .b{color:var(--grey-head)}
.service{position:absolute;top:828px;width:311px;height:360px;background:var(--white);box-shadow:0 2px 12px rgba(0,0,0,.08);text-align:center}
.service-photo{height:182px}
.service-icon{position:absolute;left:123px;top:148px;width:65px;height:65px;border-radius:50%;background:var(--blue-light);border:3px solid #fff;display:flex;align-items:center;justify-content:center}
.service h3{margin-top:43px;font-weight:500;font-size:18px;color:var(--ink)}
.service p{margin:12px 20px 0;font-weight:300;font-size:15.5px;line-height:23px;color:var(--text)}
.select{position:absolute;left:0;width:100%;top:313px;font-weight:500;font-size:17px;color:var(--blue);display:flex;justify-content:center;align-items:center;gap:8px}
.contact{position:absolute;left:0;top:1302px;width:1200px;height:596px;background:var(--panel);border-top-left-radius:230px 240px}
.field{position:absolute;background:#fff;border:1px solid #e3e3e3;border-radius:3px;font-size:13px;color:#666;display:flex;align-items:center;gap:8px;padding-left:20px}
.field.area{align-items:flex-start;padding:24px 28px}
.contact-email{position:absolute;top:1740px;width:1200px;text-align:center;font-size:17px;font-weight:500;color:#666}
.submit{position:absolute;left:456px;top:1776px;width:288px;height:49px;border-radius:25px;background:linear-gradient(#57a9e6,#1d7cc4);color:#fff;font-weight:500;font-size:17px;display:flex;align-items:center;justify-content:center}
.client{position:absolute;top:2053px;width:198px;height:86px;border:1px solid #e6e6e6;border-radius:12px;background:#fff;display:flex;align-items:center;justify-content:center;font-weight:500;font-size:17px;color:var(--blue)}
.badge{width:140px;height:56px;background:#2b2d31;border-radius:4px}
.arrow{position:absolute;top:2080px;width:32px;height:32px;border-radius:50%;background:#fff;box-shadow:0 1px 6px rgba(0,0,0,.18);display:flex;align-items:center;justify-content:center}
.footer{position:absolute;left:0;top:2229px;width:1200px;height:353px;background:var(--footer);border-top-right-radius:270px 240px;color:#fff}
.footer-brand{position:absolute;left:110px;top:90px;width:160px;text-align:center}
.footer-brand .dot{width:40px;height:40px;border-radius:50%;background:var(--blue-light);margin:0 auto 8px}
.footer-brand .name{font-family:'Oswald',sans-serif;font-weight:700;font-size:30px;line-height:34px;color:var(--blue-light)}
.footer-brand .licence{margin-top:18px;font-size:14px}
.divider{position:absolute;top:90px;width:1px;height:158px;background:#383b47}
.col{position:absolute;top:88px}
.col h4{font-weight:500;font-size:17px;margin-bottom:20px}
.col li{list-style:none;font-size:14.5px;line-height:26.5px;display:flex;align-items:center;gap:12px}
.col .social li{line-height:33.5px}
.soc{width:29px;height:29px;border-radius:50%;background:#2f323e}
.ico{width:14px;display:inline-flex;justify-content:center}
.col a{color:#fff}
.copy-line{position:absolute;left:100px;top:284px;width:1000px;height:1px;background:#30333f}
.copy{position:absolute;top:312px;width:1200px;text-align:center;font-size:14px}
</style>
</head>
<body>
<div class="page">
  <header class="hero">
    <svg class="menu-toggle" width="18" height="16" viewBox="0 0 18 16"><rect y="1" width="18" height="3" fill="#fff"/><rect y="7" width="18" height="3" fill="#fff"/><rect y="13" width="18" height="3" fill="#fff"/></svg>
    <div class="brand"><span class="brand-dot"></span><span class="brand-name">Maple n Brook</span></div>
    <div class="tagline">END OF LEASE SERVICES<span>|</span>LICENSED PEST CONTROL</div>
  </header>

  <h2 class="section-title" style="top:740px"><span class="a">WHAT</span> <span class="b">WE DO</span></h2>

  <article class="service" style="left:111px">
    <div class="service-photo" role="img" aria-label="Cleaner mopping an office floor" style="background:linear-gradient(135deg,#e9e6e1,#6b4a35 70%,#3a2a22)"></div>
    <div class="service-icon"><svg width="30" height="30" viewBox="0 0 30 30" fill="none" stroke="#fff" stroke-width="1.6"><path d="M8 16h14l-2 10H10z"/><path d="M20 4l-6 12"/><path d="M5 6l1 2 2 1-2 1-1 2-1-2-2-1 2-1z"/></svg></div>
    <h3>Cleaning</h3>
    <p>All interior cleaning carried out to property management requirements</p>
    <div class="select">SELECT <svg width="16" height="16" viewBox="0 0 16 16" fill="none" stroke="#1778c0" stroke-width="1.8"><rect x="1" y="3" width="11" height="11" rx="2"/><path d="M4 8l3 3 8-9"/></svg></div>
  </article>
  <article class="service" style="left:444px">
    <div class="service-photo" role="img" aria-label="Steam cleaner wand on carpet" style="background:linear-gradient(135deg,#3d3f42,#bdb8ae 40%,#d9d6cf)"></div>
    <div class="service-icon"><svg width="30" height="30" viewBox="0 0 30 30" fill="none" stroke="#fff" stroke-width="1.6"><rect x="5" y="10" width="20" height="16" rx="2"/><rect x="11" y="4" width="12" height="6"/><rect x="9" y="15" width="5" height="7"/><path d="M17 15h5M17 19h5"/></svg></div>
    <h3>Carpet Cleaning</h3>
    <p>Carpet Steam cleaning to Australian Standard As 3733:1995</p>
    <div class="select">SELECT <svg width="14" height="14" viewBox="0 0 14 14" fill="none" stroke="#1778c0" stroke-width="1.8"><rect x="1" y="1" width="12" height="12" rx="2"/></svg></div>
  </article>
  <article class="service" style="left:777px">
    <div class="service-photo" role="img" aria-label="Technician spraying for pests in a home" style="background:linear-gradient(135deg,#b49a86,#e6e1da 50%,#f1ede8)"></div>
    <div class="service-icon"><svg width="30" height="30" viewBox="0 0 30 30" fill="none" stroke="#fff" stroke-width="1.6"><ellipse cx="15" cy="17" rx="5" ry="8"/><circle cx="15" cy="8" r="2.5"/><path d="M10 13l-5-3M10 18H4M10 22l-5 4M20 13l5-3M20 18h6M20 22l5 4"/></svg></div>
    <h3>Pest Control</h3>
    <p>Mandatary requirement for Pets on Premises</p>
    <div class="select">SELECT <svg width="14" height="14" viewBox="0 0 14 14" fill="none" stroke="#1778c0" stroke-width="1.8"><rect x="1" y="1" width="12" height="12" rx="2"/></svg></div>
  </article>

  <section class="contact"></section>
  <h2 class="section-title" style="top:1350px"><span class="a">CONTACT</span> <span class="b">US</span></h2>
  <div class="field" style="left:125px;top:1454px;width:467px;height:53px">&#128100;&#xFE0E; First Name</div>
  <div class="field" style="left:125px;top:1520px;width:467px;height:53px">&#128100;&#xFE0E; Sur Name</div>
  <div class="field" style="left:125px;top:1585px;width:467px;height:53px">&#9993;&#xFE0E; Email Address</div>
  <div class="field" style="left:125px;top:1650px;width:467px;height:53px">&#9742;&#xFE0E; Phone Number</div>
  <div class="field area" style="left:608px;top:1454px;width:468px;height:249px">&#128488;&#xFE0E; suburb</div>
  <div class="contact-email">info@maplenbrook.com.au</div>
  <div class="submit">SUBMIT</div>

  <h2 class="section-title" style="top:1955px"><span class="b">OUR</span> <span class="a">CLIENTS</span></h2>
  <div class="arrow" style="left:77px"><svg width="8" height="12"><path d="M8 0v12L0 6z" fill="#222"/></svg></div>
  <div class="client" style="left:148px"><div class="badge"></div></div>
  <div class="client" style="left:384px">Vexlo Systems</div>
  <div class="client" style="left:620px">Tarn Training</div>
  <div class="client" style="left:856px">Coastal Eco College</div>
  <div class="arrow" style="left:1090px"><svg width="8" height="12"><path d="M0 0v12L8 6z" fill="#222"/></svg></div>

  <footer class="footer">
    <div class="footer-brand"><div class="dot"></div><div class="name">MAPLE N<br>BROOK</div><div class="licence">Pest Licence: 4718263</div></div>
    <div class="divider" style="left:305px"></div>
    <div class="col" style="left:377px"><h4>QUICK LINKS</h4><ul><li>Home</li><li>What We Do</li><li>Clients</li><li>Contact</li></ul></div>
    <div class="divider" style="left:537px"></div>
    <div class="col" style="left:615px"><h4>CONTACT INFO</h4><ul>
      <li><span class="ico">&#9742;&#xFE0E;</span>(888) 888-8888</li>
      <li><span class="ico">&#9113;</span>(888) 888-888</li>
      <li><span class="ico">&#9993;&#xFE0E;</span><a>info@maplenbrook.com</a></li>
      <li style="line-height:16px;align-items:flex-start;margin-top:6px"><span class="ico"><svg width="10" height="14" viewBox="0 0 10 14"><path d="M5 0a5 5 0 0 0-5 5c0 4 5 9 5 9s5-5 5-9a5 5 0 0 0-5-5zm0 7a2 2 0 1 1 0-4 2 2 0 0 1 0 4z" fill="#fff"/></svg></span>#2868 Lorem ipsum dolor sit<br>amet, consectetur</li></ul></div>
    <div class="divider" style="left:875px"></div>
    <div class="col" style="left:952px"><h4>FOLLOW US</h4><ul class="social">
      <li><span class="soc"></span>Chatter</li><li><span class="soc"></span>Chirper</li><li><span class="soc"></span>Circles</li><li><span class="soc"></span>Linkwork</li></ul></div>
    <div class="copy-line"></div>
    <div class="copy">Copyrights © maplenbrook &nbsp; 2021 | Allrights Reserved</div>
  </footer>
</div>
</body>
</html>
```